zorvan lumet website design

An IT support and IT Security Company - just use dummy text for now for the design. Examples of sites we like the looks and feel of but need it more professional feel are like: www.kelbrovault.uk.com , www.pravok.co.uk, www.quenthardy.com/professional/, www.vur.com, www.melvish.com,

Best to message me if you have any questions

Target Market(s)

small to medium UK based companies that require IT support services

Industry/Entity Type

It Company

Contact Information for Business Card

use dummy name, telephone and email for now, will provide details later.

Logo Text

zorvan lumet (and then below the logo it should say "your IT, networks and security partner")

Coding

Coded - Design and coding required

Number of Pages Required

5+ page

Colors

Designer to choose colors to be used in the design.

Requirements
Must have
• must be professional, yet simple and clear that this is a serious IT support and IT security company.
Nice to have
• 1)The website homepage must have professional quality pictures of IT support or London city skyline or any picture that projects friendly business partners, professionalism and ready to serve.
• 2) Home page needs to include tabs for following pages 'Services' , 'About Us' , 'Contact Us' 'Home'
• 3) Website built customised using wordpress is ideal and easy for us to manage.
• more room for boxed options from homepage (with pic or image in background)
Should not have
• no checkout trolleys or payment options.

```html
<!DOCTYPE html>
<html lang="en">
<head>
<meta charset="utf-8">
<title>zorvan lumet – IT support and IT security</title>
<link rel="stylesheet" href="https://fonts.googleapis.com/css2?family=Montserrat:wght@500;600;700&family=Lato:wght@400;700&display=swap">
<style>
:root{
  --blue:#29a7d4;
  --blue-deep:#1a86c0;
  --blue-light:#3db8e2;
  --heading-blue:#27a2d2;
  --ink:#555a60;
  --ink-dark:#444a50;
  --footer-blue:#2aabd7;
  --footer-dark:#2d2f33;
  --bar-dark:#232427;
  --white:#ffffff;
}
*{box-sizing:border-box;margin:0;padding:0}
html,body{width:1200px;height:3273px;overflow:hidden;background:var(--white)}
body{position:relative;font-family:"Lato",Arial,sans-serif;color:var(--ink)}
.abs{position:absolute}
h1,h2,h3,.brand{font-family:"Montserrat",Arial,sans-serif}

/* hero */
.hero{left:0;top:0;width:1200px;height:655px;
  background:linear-gradient(115deg,var(--blue-deep) 0%,var(--blue) 55%,var(--blue-light) 100%);
  clip-path:polygon(0 0,100% 0,100% 524px,0 655px)}
.brand{color:var(--white);font-weight:600;font-size:40px;letter-spacing:.5px;white-space:nowrap}
.site-brand{left:78px;top:44px}
.nav{right:76px;top:48px;display:flex;align-items:center;gap:34px;list-style:none}
.nav a{color:var(--white);text-decoration:none;font-family:"Lato",Arial,sans-serif;font-size:17px;letter-spacing:.5px}
.nav .nav-contact{display:block;background:var(--white);color:var(--blue);padding:12px 38px;border-radius:26px;font-weight:700}
.hero-title{left:78px;top:236px;width:460px;color:var(--white);font-size:31px;line-height:1.55;font-weight:600}
.btn-more{left:78px;top:356px;width:186px;height:44px;border-radius:22px;background:var(--white);color:var(--blue);
  font-size:17px;font-weight:700;letter-spacing:.5px;display:flex;align-items:center;justify-content:center;text-decoration:none}

.monitor{left:600px;top:196px;width:520px;height:340px;border-radius:10px;background:#1d1f24;padding:14px}
.monitor-screen{width:100%;height:100%;border-radius:4px;background:radial-gradient(circle at 45% 55%,#3a79a8 0%,#1d2d44 60%,#0e151f 100%)}
.monitor-chin{left:600px;top:536px;width:520px;height:20px;background:#c9ccd0;border-radius:0 0 8px 8px}
.monitor-stand{left:800px;top:556px;width:120px;height:55px;background:linear-gradient(#b9bcc1,#e3e5e8);clip-path:polygon(15% 0,85% 0,100% 100%,0 100%)}
.phone-small{left:517px;top:327px;width:146px;height:310px;border-radius:22px;background:#f1f2f4;border:2px solid #c9ccd0;padding:42px 9px 52px}
.phone-small .screen{width:100%;height:100%;background:#fafbfc;display:flex;flex-direction:column;align-items:center;justify-content:flex-end;padding-bottom:22px}
.phone-small .screen span{font-family:"Montserrat",Arial,sans-serif;color:var(--blue);font-weight:600;font-size:15px;white-space:nowrap}

/* welcome */
.welcome{left:0;top:745px;width:1200px;text-align:center}
.section-title{color:var(--heading-blue);font-weight:700;font-size:42px}
.welcome p{width:780px;margin:20px auto 0;font-size:14px;line-height:1.75;color:var(--ink)}
.welcome p + p{margin-top:14px}

/* features */
.band{left:0;width:1200px}
.feature h2{color:var(--ink-dark);font-weight:600;font-size:32px}
.feature p{font-size:14px;line-height:1.78;margin-top:14px;color:var(--ink)}
.feature-security{left:78px;top:1288px;width:400px}
.feature-support{left:703px;top:1940px;width:410px}
.phone-large{left:605px;top:1150px;width:268px;height:563px;border-radius:40px;background:#f3f4f6;border:3px solid #c4c7cc;padding:72px 14px 78px}
.phone-large .screen{width:100%;height:100%;background:linear-gradient(160deg,#3c8ee0,#1f4fa8 60%,#173a80)}
.laptop{left:78px;top:1916px;width:583px;height:305px}
.laptop-lid{left:82px;top:0;width:420px;height:280px;border-radius:12px 12px 0 0;background:#d8dadd;padding:14px}
.laptop-lid .screen{width:100%;height:100%;background:radial-gradient(circle at 50% 45%,#4a6a86,#1e2a38 70%)}
.laptop-base{left:0;top:280px;width:583px;height:25px;background:linear-gradient(#d5d7da,#9fa3a8);clip-path:polygon(4% 0,96% 0,100% 60%,95% 100%,5% 100%,0 60%)}

/* blog */
.blog-title{left:0;top:2420px;width:1200px;text-align:center}
.blog-card{top:2505px;width:500px;height:292px}
.blog-card .panel{left:0;top:0;width:260px;height:292px;background:var(--blue);padding:46px 0 0 20px;color:var(--white)}
.blog-card .panel-text{width:200px}
.blog-card .date{font-size:14px;display:flex;align-items:center;gap:8px}
.blog-card h3{font-size:19px;line-height:1.5;font-weight:600;margin-top:10px}
.blog-card p{font-size:14px;line-height:1.75;margin-top:10px}
.blog-card .photo{left:238px;top:12px;width:262px;height:262px;box-shadow:0 2px 8px rgba(0,0,0,.25)}

/* footer */
.footer{left:0;top:2917px;width:1200px;height:291px;background:var(--footer-blue)}
.footer-brand{left:78px;top:2898px;width:321px;height:135px;background:var(--footer-dark);display:flex;align-items:center;justify-content:center;box-shadow:0 4px 10px rgba(0,0,0,.25)}
.footer-brand .brand{font-size:36px}
.newsletter-title{left:78px;top:3066px;color:var(--white);font-family:"Lato",Arial,sans-serif;font-size:23px;font-weight:700}
.newsletter-field{left:78px;top:3110px;width:321px;height:45px;border:1px solid rgba(255,255,255,.7);display:flex;align-items:center;justify-content:space-between;padding:0 16px;color:var(--white);font-size:13px;font-style:italic}
.footer-col h3{font-family:"Lato",Arial,sans-serif;color:#2d6f8c;font-size:23px;font-weight:700}
.footer-col ul{list-style:none;margin-top:24px}
.footer-col li{display:flex;align-items:flex-start;gap:14px;color:var(--white);font-size:15px;line-height:1.6;margin-bottom:12px}
.services-col{left:452px;top:2970px}
.contact-col{left:803px;top:2970px;width:300px}
.contact-col li{margin-bottom:18px}
.bottom-bar{left:0;top:3208px;width:1200px;height:65px;background:var(--bar-dark);color:var(--white);font-size:15px;padding:0 78px;display:flex;align-items:center;justify-content:space-between}
.to-top{width:46px;height:46px;border-radius:50%;border:2px solid var(--blue);display:flex;align-items:center;justify-content:center}
</style>
</head>
<body>

<!-- hero -->
<div class="abs hero"></div>
<div class="abs brand site-brand">zorvan lumet</div>
<ul class="abs nav">
  <li><a href="#">HOME</a></li>
  <li><a href="#">ABOUT</a></li>
  <li><a href="#">SERVICES</a></li>
  <li><a href="#" class="nav-contact">CONTACT</a></li>
</ul>
<h1 class="abs hero-title">Lorem Ipsum is simply dummy text of the.</h1>
<a class="abs btn-more" href="#">KNOW MORE</a>

<div class="abs monitor"><div class="monitor-screen" role="img" aria-label="Hand touching a screen of network and device icons"></div></div>
<div class="abs monitor-chin"></div>
<div class="abs monitor-stand"></div>
<div class="abs phone-small"><div class="screen" role="img" aria-label="Phone screen showing a padlock and the company name"><span>zorvan lumet</span></div></div>

<!-- welcome -->
<section class="abs welcome">
  <h2 class="section-title">Welcome to zorvan lumet</h2>
  <p>Lorem Ipsum is simply dummy text of the printing and typesetting industry. Lorem Ipsum has been the industry's standard dummy text ever since the 1500s, when an unknown printer took a galley of type and scrambled it to make a type specimen book.</p>
  <p>It has survived not only five centuries, but also the leap into electronic typesetting, remaining essentially unchanged. It was popularised in the 1960s with the release of Tarvell sheets containing Lorem Ipsum passages, and more recently with desktop publishing software like Quillbase Pager including versions of Lorem Ipsum.</p>
</section>

<!-- feature bands -->
<svg class="abs band" style="top:1015px" width="1200" height="775" viewBox="0 0 1200 775" aria-hidden="true">
  <defs><linearGradient id="bandA" x1="0" y1="0" x2="1" y2="1"><stop offset="0" stop-color="#2b9fd3"/><stop offset="1" stop-color="#1a7fbf"/></linearGradient></defs>
  <polygon points="775,105 1200,0 1200,680 985,775 860,590 690,440" fill="url(#bandA)"/>
</svg>
<div class="abs feature feature-security">
  <h2>IT security</h2>
  <p>Lorem Ipsum is simply dummy text of the printing and typesetting industry. Lorem Ipsum has been the industry's standard dummy text ever since the 1500s, when an unknown printer took a galley of type and scrambled it to make a type specimen book.</p>
  <p>It has survived not only five centuries, but also the leap into electronic typesetting, remaining essentially unchanged.</p>
</div>
<div class="abs phone-large"><div class="screen" role="img" aria-label="Phone screen with a padlock over a blue circuit board"></div></div>

<svg class="abs band" style="top:1670px" width="1200" height="655" viewBox="0 0 1200 655" aria-hidden="true">
  <defs><linearGradient id="bandB" x1="0" y1="0" x2="1" y2="1"><stop offset="0" stop-color="#1a7fbf"/><stop offset="1" stop-color="#2aa6d6"/></linearGradient></defs>
  <polygon points="0,70 270,0 540,230 650,380 560,655 0,655" fill="url(#bandB)"/>
</svg>
<div class="abs feature feature-support">
  <h2>IT support</h2>
  <p>Lorem Ipsum is simply dummy text of the printing and typesetting industry. Lorem Ipsum has been the industry's standard dummy text ever since the 1500s, when an unknown printer took a galley of type and scrambled it to make a type specimen book.</p>
  <p>It has survived not only five centuries, but also the leap into electronic typesetting, remaining essentially unchanged.</p>
</div>
<div class="abs laptop">
  <div class="abs laptop-lid"><div class="screen" role="img" aria-label="Hands holding a cloud of network and device icons"></div></div>
  <div class="abs laptop-base"></div>
</div>

<!-- blog -->
<h2 class="abs section-title blog-title">Latest Blog</h2>
<article class="abs blog-card" style="left:78px">
  <div class="abs panel"><div class="panel-text">
    <div class="date"><svg width="13" height="13" viewBox="0 0 13 13" aria-hidden="true"><rect x="1" y="2" width="11" height="10" fill="none" stroke="#fff" stroke-width="1.4"/><rect x="1" y="2" width="11" height="3" fill="#fff"/></svg>12th April 2017</div>
    <h3>Lorem Ipsum is simply dummy text.</h3>
    <p>Lorem Ipsum is simply dummy text of the printing and typesetting industry. Lorem Ipsum has been the.</p>
  </div></div>
  <div class="abs photo" role="img" aria-label="Support agent with a headset at a desk" style="background:linear-gradient(135deg,#d9dde2,#9aa6b2 60%,#5f6d7a)"></div>
</article>
<article class="abs blog-card" style="left:624px">
  <div class="abs panel"><div class="panel-text">
    <div class="date"><svg width="13" height="13" viewBox="0 0 13 13" aria-hidden="true"><rect x="1" y="2" width="11" height="10" fill="none" stroke="#fff" stroke-width="1.4"/><rect x="1" y="2" width="11" height="3" fill="#fff"/></svg>12th April 2017</div>
    <h3>Lorem Ipsum is simply dummy text.</h3>
    <p>Lorem Ipsum is simply dummy text of the printing and typesetting industry. Lorem Ipsum has been the.</p>
  </div></div>
  <div class="abs photo" role="img" aria-label="Person working at a computer showing a security shield" style="background:linear-gradient(135deg,#e8ebee,#b5c4d2 55%,#6e8194)"></div>
</article>

<!-- footer -->
<footer class="abs footer"></footer>
<div class="abs footer-brand"><span class="brand">zorvan lumet</span></div>
<div class="abs newsletter-title">Newsletter Signup</div>
<div class="abs newsletter-field"><span>Email Address</span>
  <svg width="30" height="24" viewBox="0 0 30 24" aria-hidden="true"><path d="M1 11 L29 1 L22 23 L14 15 Z" fill="#fff"/><path d="M14 15 L29 1" stroke="#2aabd7" stroke-width="1.5"/></svg>
</div>
<div class="abs footer-col services-col">
  <h3>Our services</h3>
  <ul>
    <li><svg width="14" height="14" viewBox="0 0 14 14" aria-hidden="true" style="margin-top:4px"><circle cx="7" cy="7" r="6" fill="none" stroke="#2d6f8c" stroke-width="1.4"/><path d="M6 4 L9 7 L6 10" fill="none" stroke="#2d6f8c" stroke-width="1.4"/></svg>IT security</li>
    <li><svg width="14" height="14" viewBox="0 0 14 14" aria-hidden="true" style="margin-top:4px"><circle cx="7" cy="7" r="6" fill="none" stroke="#2d6f8c" stroke-width="1.4"/><path d="M6 4 L9 7 L6 10" fill="none" stroke="#2d6f8c" stroke-width="1.4"/></svg>IT support</li>
  </ul>
</div>
<div class="abs footer-col contact-col">
  <h3>Contact Info</h3>
  <ul>
    <li><svg width="16" height="20" viewBox="0 0 16 20" aria-hidden="true" style="flex:none;margin-top:2px"><path d="M8 1 C4 1 1 4 1 8 C1 13 8 19 8 19 C8 19 15 13 15 8 C15 4 12 1 8 1 Z" fill="#2d6f8c"/><circle cx="8" cy="8" r="2.5" fill="#2aabd7"/></svg>Lorem ipsum dolor sit amet, consectetur adipiscing elit.</li>
    <li><svg width="16" height="16" viewBox="0 0 16 16" aria-hidden="true" style="flex:none;margin-top:3px"><path d="M3 1 L6 1 L7 5 L5 6.5 C6 9 7 10 9.5 11 L11 9 L15 10 L15 13 C15 14 14 15 13 15 C6 15 1 10 1 3 C1 2 2 1 3 1 Z" fill="#2d6f8c"/></svg>123 456 7890</li>
    <li><svg width="17" height="13" viewBox="0 0 17 13" aria-hidden="true" style="flex:none;margin-top:5px"><rect x="1" y="1" width="15" height="11" fill="none" stroke="#2d6f8c" stroke-width="1.4"/><path d="M1 1 L8.5 7 L16 1" fill="none" stroke="#2d6f8c" stroke-width="1.4"/></svg>info@zorvanlumet.com</li>
  </ul>
</div>
<div class="abs bottom-bar">
  <span>2018 ©zorvanlumet- All Rights Reserved.</span>
  <span class="to-top"><svg width="16" height="16" viewBox="0 0 16 16" aria-hidden="true"><path d="M8 14 L8 2 M3 7 L8 2 L13 7" fill="none" stroke="#29a7d4" stroke-width="2"/></svg></span>
</div>

</body>
</html>
```